Flyer für Großhändler für Baustoffzubehör
Zielgruppe
Wir sind Großhändler für Baustoffzubehör, unsere Kunden sind Baustoffhänder - also Wiederverkäufer. Dieser Flyer soll auf den Theken ausgelegt werden und zum Teil an Garten- und Landschaftsbauer verschickt werden.
Aufgabenstellung
Vom Design sind wir offen, auch was das DIN-Format angeht. Da vermutlich einiges an Text zusammen kommt, wird ein DIN Lang nicht ausreichen. Daher entweder DIN A4 oder DIN A4 gefaltet.
Die eigenen Bilder sagen evtl. nicht genug aus. Daher bitte auch auf Bilddatenbanken zurück greifen.
Wichtig ist zu erwähnen, dass die Imprägnierung farblos ist und der Stein (Untergrund) nicht nachdunkelt.

```html
<!DOCTYPE html>
<html lang="de">
<head>
<meta charset="utf-8">
<title>Technisches Merkblatt – Steinimprägnierung</title>
<link href="https://fonts.googleapis.com/css2?family=Cinzel:wght@600&family=Open+Sans:ital,wght@0,400;0,600;0,700;1,400&display=swap" rel="stylesheet">
<style>
:root{
  --bg:#dedede;
  --paper:#f7f7f7;
  --red:#e42229;
  --blue:#3a78c4;
  --blue-dark:#2f6cb8;
  --tint:#dfe8e8;
  --ink:#2e2e2e;
  --ink-soft:#555;
}
*{margin:0;padding:0;box-sizing:border-box}
html,body{width:1200px;height:1200px;overflow:hidden;background:var(--bg)}
body{font-family:"Open Sans",sans-serif;color:var(--ink);position:relative}
.spread{position:absolute;left:40px;top:187px;width:1120px;height:825px;display:flex;box-shadow:0 20px 40px rgba(0,0,0,.18)}
.page{position:relative;width:560px;height:825px;background:linear-gradient(160deg,#fafafa 0%,#f2f4f4 60%,#f7f7f7 100%);overflow:hidden}
.page--left{border-right:1px solid #ddd}
.page-header{position:absolute;top:36px;left:29px;right:29px;height:40px}
.brand{position:absolute;left:0;top:10px;display:flex;align-items:center;gap:5px;font-weight:700;font-size:14px;color:var(--red)}
.brand-dot{width:9px;height:9px;border-radius:50%;background:var(--red)}
.header-rule{position:absolute;left:76px;top:2px;width:1px;height:36px;background:#555}
.doc-title{position:absolute;left:99px;top:3px;font-family:"Cinzel",serif;font-weight:600;font-size:17px;line-height:15px;color:#222}
.sender{position:absolute;right:8px;top:3px;font-size:5.5px;line-height:6.5px;color:#444}
.sender b{font-weight:700}
.ribbon{position:absolute;left:0;background:var(--red);clip-path:polygon(0 0,100% 0,88% 50%,100% 100%,0 100%)}
.section-title{position:absolute;font-size:14px;color:#222;line-height:16px}
.photo{position:absolute}
.photo-frame{position:absolute;border-top:4px solid var(--red);border-left:4px solid var(--red)}
.checklist{position:absolute;left:29px;top:446px;width:262px;list-style:none;font-size:7.2px;line-height:9px;color:#333}
.checklist li{position:relative;padding-left:20px;margin-bottom:9px}
.checklist li::before{content:"";position:absolute;left:2px;top:1px;width:4px;height:7px;border-right:1.2px solid #333;border-bottom:1.2px solid #333;transform:rotate(40deg)}
.col-heading{position:absolute;left:335px;font-size:9.5px;font-weight:700;color:var(--blue-dark);letter-spacing:.3px}
.col-text{position:absolute;left:335px;width:190px;font-size:7px;line-height:9.2px;color:#333}
.footer-rule{position:absolute;left:27px;right:27px;top:763px;height:1px;background:linear-gradient(90deg,#c8d3e4,var(--blue),#c8d3e4)}
.footer{position:absolute;left:29px;right:29px;top:780px;height:14px;font-size:8px;color:#333}
.footer .phone{position:absolute;left:0;top:0;display:flex;align-items:center;gap:8px}
.footer .mail{position:absolute;right:0;top:0;display:flex;align-items:center;gap:8px}
.footer .mark{position:absolute;left:50%;top:1px;transform:translateX(-50%);font-size:7px;font-weight:700;color:var(--red)}
.bottom-band{position:absolute;left:0;right:0;bottom:0;height:17px;background:var(--blue)}
.data-table{position:absolute;left:27px;top:160px;width:505px;border-collapse:collapse;font-size:7px;line-height:9px;color:#333}
.data-table td{vertical-align:middle}
.data-table td.label{width:181px;padding-left:30px}
.data-table td.value{padding-right:30px}
.data-table tr:nth-child(odd){background:var(--tint)}
.disclaimer{position:absolute;left:27px;top:531px;width:345px;font-size:5px;line-height:6px;font-style:italic;color:#444}
.tool{position:absolute;top:529px;width:44px;height:44px;border:1.5px solid #4aa3d6;border-radius:6px;background:#fff}
.tool svg{width:100%;height:100%}
.safety-text{position:absolute;left:27px;top:656px;width:130px;font-size:7px;line-height:9px;color:#333}
.safety-text p{margin-bottom:12px}
.caption{position:absolute;right:6px;bottom:4px;background:#fff;border:1px solid #888;font-size:7px;padding:2px 5px;color:#333}
</style>
</head>
<body>
<main class="spread">

  <!-- Page 1 -->
  <section class="page page--left">
    <header class="page-header">
      <div class="brand"><span class="brand-dot"></span>KARVO</div>
      <div class="header-rule"></div>
      <h1 class="doc-title">Technisches<br>Merkblatt</h1>
      <address class="sender" style="font-style:normal"><b>KARVO-Lindner GmbH</b><br>Bauzubehör<br>Ahornweg 7<br>71234 Tannbach</address>
    </header>

    <div class="ribbon" style="top:118px;width:113px;height:31px"></div>
    <h2 class="section-title" style="left:127px;top:121px;font-weight:400">Steinimprägnierung für Kalksandstein, Ziegel,<br>Naturklinker und Natursteine</h2>

    <div class="photo-frame" style="left:29px;top:176px;width:494px;height:225px"></div>
    <div class="photo" role="img" aria-label="Wassertropfen perlen auf imprägniertem grauem Stein ab" style="left:35px;top:182px;width:494px;height:223px;background:radial-gradient(ellipse at 55% 55%,#9a958a 0%,#7c776c 45%,#5f5a51 100%)"></div>
    <svg class="photo" style="left:355px;top:293px" width="156" height="102" viewBox="0 0 156 102"><path d="M150 0V98H0" fill="none" stroke="#f2f2f2" stroke-width="7"/></svg>

    <ul class="checklist">
      <li>KARVO-Hydro-Grund bietet einen umfassenden Schutz für Mauerwerk und Fassade. Dazu gehören alkalische Baustoffe wie Putz, Mörtel, Porenbeton, industriegefertigte Ziegel, Klinker und Kalksandsteine<br>sowie Natursteine und Pflaster.</li>
      <li>Unsere Imprägnierung schützt das Mauerwerk viele Jahre zuverlässig gegen Eindringen von Wasser</li>
      <li>Hohe Eindringtiefen gewährleisten die Dauerhaftigkeit einer Hydrophobierung.</li>
      <li>Schnelle Trocknung (ca. 1 Stunde)</li>
      <li>Schützt vor Ausblühungen und Zerstörung durch wasserlösliche Schadstoffe</li>
      <li>Schützt vor Frostschäden und Befall durch Mikroorganismen.</li>
      <li>Das optische Erscheinungsbild des Untergrundes bleibt erhalten.</li>
      <li>Farbneutral - der Untergrund dunkelt nicht nach.</li>
      <li>Die Eigenschaften, vor allem die Wasserdampfdurchlässigkeit werden kaum beeinflusst.</li>
      <li>Auch als Grundierungsmittel für Silikonharzfarben und -putze, sowie anderer dispersionshaltige Farben und Putze eingesetzt. Bei fachgerechtem Einsatz wird die Haftung des Anstriches zum Untergrund verbessert.</li>
    </ul>

    <div class="photo" role="img" aria-label="Mauer aus bunten Natursteinen in Braun- und Grautönen" style="left:335px;top:442px;width:195px;height:98px;border-top:4px solid var(--blue);background:linear-gradient(135deg,#9b8068 0%,#7d7a76 50%,#8d7560 100%)"></div>

    <h3 class="col-heading" style="top:558px">ANWENDUNG</h3>
    <p class="col-text" style="top:576px">KARVO-Microgrund kann durch Rollen, Streichen, Fluten oder Airless – Spritzen appliziert werden. Zum Zeitpunkt der Hydrophobierung bzw. rundierung darf der Baustoff nicht nass sein. Der Untergrund soll nicht nur im oberflächennahen Bereich abgetrocknet sein, da Wasser in den Kapillaren ein tiefes Eindringen verhindert.</p>
    <h3 class="col-heading" style="top:663px">VERARBEITUNG</h3>
    <p class="col-text" style="top:682px">KARVO-Microgrund kann pur oder in einem Verhältnis bis max. 1 : 1 verdünnt mit Wasser, angewendet werden. Im Einzelfall am Objekt prüfen. Nicht zu behandelnde Flächen sind zu schützen.</p>

    <div class="footer-rule"></div>
    <footer class="footer">
      <span class="phone"><svg width="9" height="10" viewBox="0 0 24 24"><path fill="#e42229" d="M6.6 10.8a15 15 0 0 0 6.6 6.6l2.2-2.2c.3-.3.7-.4 1-.2 1.1.4 2.3.6 3.6.6.6 0 1 .4 1 1V20c0 .6-.4 1-1 1A17 17 0 0 1 3 4c0-.6.4-1 1-1h3.5c.6 0 1 .4 1 1 0 1.3.2 2.5.6 3.6.1.3 0 .7-.2 1z"/></svg>+49 7123 / 45 6 78-0</span>
      <span class="mark">KARVO</span>
      <span class="mail"><svg width="12" height="9" viewBox="0 0 24 18"><rect width="24" height="18" fill="#e42229"/><path d="M1 1l11 9 11-9" fill="none" stroke="#fff" stroke-width="2"/></svg>info@karvo-lindner.de</span>
    </footer>
    <div class="bottom-band"></div>
  </section>

  <!-- Page 2 -->
  <section class="page page--right">
    <header class="page-header">
      <div class="brand"><span class="brand-dot"></span>KARVO</div>
      <div class="header-rule"></div>
      <h1 class="doc-title">Technisches<br>Merkblatt</h1>
      <address class="sender" style="font-style:normal"><b>KARVO-Lindner GmbH</b><br>Bauzubehör<br>Ahornweg 7<br>71234 Tannbach</address>
    </header>

    <div class="ribbon" style="top:123px;width:110px;height:18px"></div>
    <h2 class="section-title" style="left:122px;top:124px;font-weight:400">TECHNISCHE DATEN</h2>

    <table class="data-table">
      <tr style="height:63px"><td class="label">Einsatzgebiet</td><td class="value">Hydrophobierungs- und Grundierungsmittel für mineralische Untergründe; Hydrophobierungsmittel für werkseitig hergestellte Baustoffe z.B. aus Ton, Porenbeton, Faserzement, Klinker, Beton und Kalksandstein</td></tr>
      <tr style="height:36px"><td class="label">Zusammensetzung</td><td class="value">wässrige, lösemittelfreie Silsan – Emulsion</td></tr>
      <tr style="height:33px"><td class="label">Farbe</td><td class="value">milchig-weiß, feinteilig</td></tr>
      <tr style="height:35px"><td class="label">Reinigen der Werkzeuge</td><td class="value">sofort nach Gebrauch mit Wasser</td></tr>
      <tr style="height:33px"><td class="label">Gebindegröße</td><td class="value">5 od. 10 ltr. Kunststoffkanister</td></tr>
      <tr style="height:35px"><td class="label">Trocknungszeit</td><td class="value">Begehbar nach ca. 1 Stunde</td></tr>
      <tr style="height:33px"><td class="label">Verbrauch</td><td class="value">ca. 70-200 ml/m² je nach Saugfähigkeit des Untergrundes</td></tr>
      <tr style="height:43px"><td class="label">Verarbeitungstemperatur</td><td class="value">mindestens + 5°C für Untergrund und Luft bei der Verarbeitung und Trocknung</td></tr>
      <tr style="height:44px"><td class="label">VOC-Gehalt</td><td class="value">EU-Grenzwert Für dieses Produkt: (Kat. h) 30g/l VOC (2010) Dieses Produkt enthält max. &lt; 30g/l VOC</td></tr>
    </table>

    <p class="disclaimer">Stand 03/2023 Mit Erscheinen dieses Merkblattes verlieren alle früheren Ausgaben ihre Gültigkeit. Für die Güte unseres Materials garantieren wir im Rahmen unserer Verkaufs- und Lieferbedingungen. Aufgrund der vielen unterschiedlichen Untergründe und Anwendungsverhältnisse können wir jedoch keine Haftung für das Verarbeitungsergebnis übernehmen. Wir empfehlen deshalb, durch Eigenversuche die jeweilige Anwendung zu überprüfen.</p>

    <div class="tool" style="left:380px"><svg viewBox="0 0 44 44"><rect x="11" y="8" width="20" height="8" rx="2" fill="#4aa3d6"/><path d="M31 12h4v9H22v5" fill="none" stroke="#4aa3d6" stroke-width="2"/><rect x="20" y="26" width="4" height="12" fill="#4aa3d6"/></svg></div>
    <div class="tool" style="left:433px"><svg viewBox="0 0 44 44"><rect x="20" y="6" width="5" height="16" fill="#4aa3d6"/><rect x="17" y="21" width="11" height="5" fill="#4aa3d6"/><path d="M16 26h13l1 12H15z" fill="#4aa3d6"/></svg></div>
    <div class="tool" style="left:487px"><svg viewBox="0 0 44 44"><path d="M22 12h14v8h-5v8h-5v-8h-4z" fill="#4aa3d6"/><path d="M20 16l-10-4M20 16l-10 0M20 16l-10 4" stroke="#9fd0ea" stroke-width="1" stroke-dasharray="1.5 1.5"/><text x="22" y="40" font-size="6" text-anchor="middle" fill="#4aa3d6" font-family="Open Sans, sans-serif">airless</text></svg></div>

    <div class="ribbon" style="top:586px;width:110px;height:17px"></div>
    <h2 class="section-title" style="left:122px;top:586px;font-weight:400">SICHERHEITSHINWEIS</h2>

    <div class="safety-text">
      <p>Berührung mit Augen und der Haut vermeiden</p>
      <p>Darf nicht in die Hände von Kindern gelangen</p>
    </div>

    <div class="photo-frame" style="left:199px;top:622px;width:326px;height:130px"></div>
    <div class="photo" role="img" aria-label="Imprägnierter Pflasterstein mit abperlendem Wasser" style="left:205px;top:628px;width:326px;height:129px;background:radial-gradient(ellipse at 45% 60%,#b5aaa0 0%,#a3968b 50%,#8e8178 100%)">
      <span class="caption">Hier wurde ein Pflasterstein imprägniert.</span>
    </div>

    <div class="footer-rule"></div>
    <footer class="footer">
      <span class="phone"><svg width="9" height="10" viewBox="0 0 24 24"><path fill="#e42229" d="M6.6 10.8a15 15 0 0 0 6.6 6.6l2.2-2.2c.3-.3.7-.4 1-.2 1.1.4 2.3.6 3.6.6.6 0 1 .4 1 1V20c0 .6-.4 1-1 1A17 17 0 0 1 3 4c0-.6.4-1 1-1h3.5c.6 0 1 .4 1 1 0 1.3.2 2.5.6 3.6.1.3 0 .7-.2 1z"/></svg>+49 7123 / 45 6 78-0</span>
      <span class="mark">KARVO</span>
      <span class="mail"><svg width="12" height="9" viewBox="0 0 24 18"><rect width="24" height="18" fill="#e42229"/><path d="M1 1l11 9 11-9" fill="none" stroke="#fff" stroke-width="2"/></svg>info@karvo-lindner.de</span>
    </footer>
    <div class="bottom-band"></div>
  </section>

</main>
</body>
</html>
```